Tall Fern Roofing Business Card

Need a business card with the logo that was designed here

Contact Information for Business Card

Name, Title, Phone, Email, Website, Company name

```html
<!DOCTYPE html>
<html lang="en">
<head>
<meta charset="utf-8">
<title>Tall Fern Roofing – Business Card</title>
<link rel="stylesheet" href="https://fonts.googleapis.com/css2?family=Great+Vibes&family=Poppins:wght@400;600;700&display=swap">
<style>
  :root {
    --canvas: #2b2b2d;
    --card-white: #ffffff;
    --brand-blue: #1f6fc0;
    --back-blue: #2c70ae;
    --brand-grey: #8b8d90;
    --ink: #3a3a3c;
    --rule: #9a9a9a;
  }
  * { margin: 0; padding: 0; box-sizing: border-box; }
  html, body {
    width: 1200px; height: 1108px; overflow: hidden;
    background: var(--canvas);
    font-family: "Poppins", sans-serif;
  }
  .stage {
    position: relative; width: 1200px; height: 1108px;
    display: flex; justify-content: center; align-items: center; gap: 70px;
  }
  .card {
    width: 340px; height: 595px; border-radius: 24px;
    position: relative; overflow: hidden;
    box-shadow: 0 14px 30px rgba(0,0,0,0.45);
  }
  .card-front { background: var(--card-white); }
  .card-back { background: var(--back-blue); }

  .brand-mark {
    position: absolute; top: 130px; left: 0; right: 0;
    display: flex; justify-content: center; align-items: center; gap: 10px;
    color: var(--brand-blue); font-weight: 600; font-size: 27px; letter-spacing: 0.5px;
  }
  .brand-mark .brand-square {
    width: 16px; height: 16px; background: var(--brand-blue); flex: none;
  }

  .person {
    position: absolute; top: 345px; left: 0; right: 0; text-align: center;
  }
  .person-name { line-height: 1; }
  .person-first {
    font-family: "Great Vibes", cursive; color: var(--brand-blue); font-size: 44px;
  }
  .person-last {
    font-weight: 700; color: var(--brand-grey); font-size: 24px; margin-left: 6px;
  }
  .person-title {
    color: var(--brand-blue); font-size: 15px; letter-spacing: 0.5px; margin-top: 6px;
  }

  .contact-rule {
    position: absolute; top: 452px; left: 30px; right: 30px;
    display: flex; align-items: center; gap: 8px;
  }
  .contact-rule .line { flex: 1; height: 1px; background: var(--rule); }
  .contact-icon {
    width: 26px; height: 26px; background: var(--brand-blue); border-radius: 3px;
    display: flex; align-items: center; justify-content: center;
  }
  .contact-icon svg { width: 16px; height: 16px; }

  .contact-list {
    position: absolute; top: 490px; left: 0; right: 0;
    list-style: none; text-align: center; color: var(--ink);
    font-size: 16px; line-height: 1.45;
  }

  .back-pattern {
    position: absolute; inset: 0;
    background: linear-gradient(135deg, #3579b8 0%, #2c70ae 50%, #25649c 100%);
  }
  .back-mark {
    position: absolute; top: 360px; left: 0; right: 0;
    display: flex; justify-content: center; align-items: center; gap: 8px;
    color: #ffffff; font-weight: 600; font-size: 18px;
  }
  .back-mark .brand-square { width: 11px; height: 11px; background: #ffffff; }
</style>
</head>
<body>
<main class="stage">
  <section class="card card-front" aria-label="Card front">
    <div class="brand-mark"><span class="brand-square"></span><span>Tall Fern Roofing</span></div>

    <div class="person">
      <p class="person-name"><span class="person-first">Daniel</span><span class="person-last">BROOKS</span></p>
      <p class="person-title">MANAGING DIRECTOR</p>
    </div>

    <div class="contact-rule">
      <span class="line"></span>
      <span class="contact-icon" aria-label="Phone">
        <svg viewBox="0 0 24 24" fill="#fff"><path d="M6.6 10.8a15.1 15.1 0 0 0 6.6 6.6l2.2-2.2a1 1 0 0 1 1-.25 11.4 11.4 0 0 0 3.6.57 1 1 0 0 1 1 1V20a1 1 0 0 1-1 1A17 17 0 0 1 3 4a1 1 0 0 1 1-1h3.5a1 1 0 0 1 1 1c0 1.25.2 2.45.57 3.6a1 1 0 0 1-.25 1z"/></svg>
      </span>
      <span class="contact-icon" aria-label="Email">
        <svg viewBox="0 0 24 24" fill="none" stroke="#fff" stroke-width="2"><rect x="3" y="5" width="18" height="14" rx="1"/><path d="M3 6l9 7 9-7"/></svg>
      </span>
      <span class="contact-icon" aria-label="Website">
        <svg viewBox="0 0 24 24" fill="none" stroke="#fff" stroke-width="2"><circle cx="12" cy="12" r="9"/><path d="M3 12h18M12 3c3 3 3 15 0 18M12 3c-3 3-3 15 0 18"/></svg>
      </span>
      <span class="line"></span>
    </div>

    <ul class="contact-list">
      <li>044-987 654 321</li>
      <li>info@tallfernroof.com</li>
      <li>www.tallfernroof.com</li>
    </ul>
  </section>

  <section class="card card-back" aria-label="Card back">
    <div class="back-pattern" role="img" aria-label="Repeating tone-on-tone brand pattern across the blue card back"></div>
    <div class="back-mark"><span class="brand-square"></span><span>Tall Fern Roofing</span></div>
  </section>
</main>
</body>
</html>
```